Business Card for a New Zealand IT Startup

I need a business card for VELTA Holdings. We are a young startup based in New Zealand working in internet marketing and web development. The design should have some element connected to New Zealand, such as wave, koru or silver fern, just don't use a kiwi bird.

```html
<!DOCTYPE html>
<html lang="en">
<head>
<meta charset="utf-8">
<title>VELTA Holdings — Business Card</title>
<link rel="stylesheet" href="https://fonts.googleapis.com/css2?family=Roboto:wght@400;500;700&display=swap">
<style>
  :root {
    --brand-blue: #0a6eb8;
    --brand-orange: #f15a24;
    --card-white: #ffffff;
    --page-bg: #ecebe8;
    --ink-light: #ffffff;
  }
  * { margin: 0; padding: 0; box-sizing: border-box; }
  html, body {
    width: 1125px; height: 1200px; overflow: hidden;
    background: var(--page-bg);
    font-family: "Roboto", Arial, sans-serif;
  }
  .canvas { position: relative; width: 1125px; height: 1200px; }
  .card {
    position: absolute; left: 162px; width: 800px; height: 455px;
    border-radius: 22px; overflow: hidden;
    box-shadow: 0 6px 14px rgba(0,0,0,0.25);
  }
  .card--front { top: 110px; background: var(--card-white); }
  .card--back { top: 630px; background: var(--brand-orange); }
  .card__shape { position: absolute; inset: 0; }
  .holder { position: absolute; left: 45px; top: 45px; color: var(--ink-light); }
  .holder__name { font-size: 28px; font-weight: 700; letter-spacing: 0.5px; line-height: 1.1; }
  .holder__title { font-size: 19px; font-weight: 500; margin-top: 2px; }
  .address {
    position: absolute; left: 45px; top: 220px;
    color: var(--ink-light); font-size: 18px; line-height: 24px; font-style: normal;
  }
  .contacts {
    position: absolute; left: 45px; top: 282px; list-style: none;
    color: var(--ink-light); font-size: 18px;
  }
  .contacts li { display: flex; align-items: center; height: 25.5px; }
  .contacts svg { width: 18px; height: 18px; margin-right: 12px; fill: var(--ink-light); flex: none; }
  .wordmark {
    position: absolute; left: 440px; top: 100px; width: 320px; text-align: center;
    color: var(--brand-blue); font-size: 44px; font-weight: 700; letter-spacing: 1px;
  }
  .back-mark {
    position: absolute; left: 310px; top: 100px; width: 180px; height: 180px;
    border-radius: 50%; background: var(--card-white);
  }
  .back-web {
    position: absolute; left: 0; right: 0; top: 388px; text-align: center;
    color: var(--ink-light); font-size: 18px; letter-spacing: 6px;
  }
  .back-web strong { font-weight: 700; }
</style>
</head>
<body>
<main class="canvas">
  <section class="card card--front" aria-label="Card front">
    <svg class="card__shape" viewBox="0 0 800 455" width="800" height="455" aria-hidden="true">
      <path d="M0 0 H300 C285 45 305 95 365 165 C430 240 545 320 522 398 C512 428 492 446 465 455 H0 Z" fill="var(--brand-blue)"/>
      <path d="M300 0 C285 45 305 95 365 165 C430 240 545 320 522 398" fill="none" stroke="#fff" stroke-width="4"/>
      <path d="M308 0 H322 C312 70 370 150 462 255 C372 175 296 95 308 0 Z" fill="var(--brand-orange)"/>
    </svg>

    <header class="holder">
      <h1 class="holder__name">RHYS CARTER</h1>
      <p class="holder__title">CEO/FOUNDER</p>
    </header>

    <address class="address">214 Harbour View Road<br>Wellington, New Zealand 6011</address>

    <ul class="contacts">
      <li><svg viewBox="0 0 24 24"><path d="M6.6 10.8a15 15 0 0 0 6.6 6.6l2.2-2.2c.3-.3.7-.4 1-.2 1.1.4 2.3.6 3.6.6.6 0 1 .4 1 1V20c0 .6-.4 1-1 1A17 17 0 0 1 3 4c0-.6.4-1 1-1h3.5c.6 0 1 .4 1 1 0 1.3.2 2.5.6 3.6.1.3 0 .7-.2 1z"/></svg>04 382 5170</li>
      <li><svg viewBox="0 0 24 24"><path d="M7 1h10a2 2 0 0 1 2 2v18a2 2 0 0 1-2 2H7a2 2 0 0 1-2-2V3a2 2 0 0 1 2-2zm0 3v14h10V4zm5 15.5a1.2 1.2 0 1 0 0 2.4 1.2 1.2 0 0 0 0-2.4z"/></svg>021 947 3306</li>
      <li><svg viewBox="0 0 24 24"><path d="M6 2h9l3 3v5H6zM3 11h18a2 2 0 0 1 2 2v7a2 2 0 0 1-2 2H3a2 2 0 0 1-2-2v-7a2 2 0 0 1 2-2zm3 4v2h12v-2z"/></svg>04 382 5171</li>
      <li><svg viewBox="0 0 24 24"><path d="M2 5h20v14H2zm2 2v.5l8 5.5 8-5.5V7zm0 3v7h16v-7l-8 5.5z"/></svg>rhys@veltaholdings.com</li>
      <li><svg viewBox="0 0 24 24"><path d="M12 2a10 10 0 1 0 0 20 10 10 0 0 0 0-20zm-1 17.9A8 8 0 0 1 4.2 10.5L9 15v1a2 2 0 0 0 2 2zm6.9-2.5A2 2 0 0 0 16 16h-1v-3a1 1 0 0 0-1-1H8v-2h2a1 1 0 0 0 1-1V7h2a2 2 0 0 0 2-2v-.4a8 8 0 0 1 2.9 12.8z"/></svg>www.veltaholdings.com</li>
    </ul>

    <p class="wordmark">VELTA Holdings</p>
  </section>

  <section class="card card--back" aria-label="Card back">
    <div class="back-mark" aria-hidden="true"></div>
    <p class="back-web">www.<strong>veltaholdings</strong>.com</p>
  </section>
</main>
</body>
</html>
```